Alloy wheel repair business needs a website

Install logo previously purchased from makerhive, toolbar with dropdowns. services, gallery, clients , contact ect
Maybe mission statment

Target Market(s)

vehicle owners, auto dealers,insurance companies,

Industry/Entity Type

Alloy Wheel Repair

Coding

Coded - Design and coding required

Number of Pages Required

4 page

Font styles to use
Sans Serif

Colors
0054AA
0677BA
7BADD7
CADEEF
E8F1F8

```html
<!DOCTYPE html>
<html lang="en">
<head>
<meta charset="utf-8">
<title>Rimcraft Wheel Works</title>
<link href="https://fonts.googleapis.com/css2?family=Michroma&family=Arimo:wght@400;700&family=Noto+Sans:wght@400;500&display=swap" rel="stylesheet">
<style>
:root{
  --blue:#4688c9;
  --blue-deep:#0677BA;
  --blue-soft:#7BADD7;
  --blue-pale:#CADEEF;
  --blue-wash:#E8F1F8;
  --ink:#111;
  --text:#333;
  --white:#fff;
  --black:#000;
  --star:#f2c200;
}
*{margin:0;padding:0;box-sizing:border-box}
html,body{width:1200px;height:3557px;overflow:hidden;background:var(--white)}
body{position:relative;font-family:"Arimo",sans-serif;color:var(--text)}
.abs{position:absolute}
.display{font-family:"Michroma",sans-serif;font-style:italic;text-transform:uppercase;font-weight:400}
.accent{color:var(--blue)}
.photo{position:absolute}

/* header */
.logo{left:100px;top:18px;display:flex;align-items:center;gap:10px;color:var(--blue-deep);font-family:"Arimo",sans-serif;font-weight:700}
.logo-mark{width:32px;height:32px;border-radius:50%;background:var(--blue-deep)}
.logo-name{font-size:24px;line-height:26px;letter-spacing:2px}
.logo-name small{display:block;font-size:12px;letter-spacing:6px;line-height:14px}
.nav{top:33px;font-size:14px;color:var(--ink)}
.nav.current{color:var(--blue)}
.nav-sep{top:33px;font-size:14px;color:var(--ink);font-family:"Arimo",sans-serif}
.contact-btn{left:968px;top:19px;width:132px;height:47px;background:var(--blue);color:var(--white);font-size:14px;display:flex;align-items:center;justify-content:center;border-radius:3px;box-shadow:0 3px 6px rgba(0,0,0,.2)}

/* hero */
.hero{left:0;top:87px;width:1200px;height:599px;border-radius:0 0 60px 60px;background:linear-gradient(90deg,#5c5a58 0%,#8a8683 40%,#6d6a68 65%,#2b2b2d 100%)}
.hero-kicker{left:104px;top:276px;font-size:22px;color:var(--white)}
.hero-title{left:97px;top:316px;font-size:38px;color:var(--white)}
.hero-text{left:98px;top:368px;width:520px;font-size:15.5px;line-height:31px;color:var(--white)}
.hero-btn{left:98px;top:443px;width:141px;height:50px;background:var(--blue);color:var(--white);font-size:14px;display:flex;align-items:center;justify-content:center;border-radius:3px}

/* about */
.about-title{left:109px;top:752px;font-size:32px;line-height:45px;color:var(--ink)}
.about-lead{left:109px;top:855px;width:410px;font-family:"Noto Sans",sans-serif;font-size:17.5px;line-height:34.5px;color:var(--ink)}
.about-body{left:577px;top:754px;width:510px;font-size:15px;line-height:31px;color:var(--text)}
.about-frame{left:507px;top:1073px;width:420px;height:358px;border:6px solid var(--blue);border-radius:4px}
.about-back{left:584px;top:1045px;width:501px;height:346px;background:linear-gradient(120deg,#6f7580,#c8ccd2 40%,#2d4f85 75%,#e8eef5)}
.about-front{left:106px;top:1109px;width:587px;height:351px;border:3px solid var(--white);background:linear-gradient(100deg,#1a1a1c,#6a4630 40%,#c59a6a 60%,#2a2a2c)}

/* services */
.services{left:0;top:1540px;width:1200px;height:578px;background:linear-gradient(180deg,#4a8acb,#4688c9 60%,#5b97d2)}
.services-title{left:0;top:1601px;width:1200px;text-align:center;font-size:31px;color:var(--white)}
.card{top:1665px;width:318px;height:373px;background:var(--white);border-radius:4px}
.card-img{left:14px;top:13px;width:291px;height:224px}
.card-tab{left:46px;top:203px;width:226px;height:40px;background:var(--white);display:flex;align-items:flex-end;justify-content:center;font-size:16px;color:var(--ink);padding-bottom:2px}
.card-text{left:0;top:257px;width:318px;text-align:center;font-size:15.5px;line-height:31px;color:var(--text)}
.card-link{left:0;top:324px;width:318px;text-align:center;font-size:13px;color:var(--blue)}
.card-link svg{vertical-align:-1px;margin-left:4px}
.slider-dot{width:26px;height:26px;border:1.5px solid var(--white);border-radius:50%;top:1839px}

/* gallery */
.gallery-title{left:0;top:2181px;width:1250px;text-align:center;font-size:31px;color:var(--ink)}
.gallery-img{top:2243px;width:235px;height:324px}
.gallery-arrow{top:2396px}

/* testimonials */
.testimonials{left:0;top:2646px;width:1200px;height:467px;background:var(--blue-wash)}
.testi-title{left:0;top:2697px;width:1200px;text-align:center;font-size:31px;color:var(--ink)}
.testi-card{top:2805px;width:311px;height:192px;background:var(--white);border-top:3px solid var(--blue);border-radius:18px;box-shadow:0 2px 6px rgba(0,0,0,.12)}
.testi-card::after{content:"";position:absolute;left:147px;bottom:-9px;width:16px;height:16px;background:var(--white);transform:rotate(45deg)}
.avatar{top:2759px;width:92px;height:92px;border-radius:50%;border:3px solid var(--white);background:linear-gradient(180deg,#d9dde2,#9aa6b4)}
.testi-text{left:0;top:70px;width:311px;text-align:center;font-size:14.5px;line-height:26px;color:#555;padding:0 22px;position:absolute}
.testi-name{top:3022px;font-size:15px;color:var(--text)}
.stars{top:3024px;color:var(--star);font-size:13px;letter-spacing:1px}

/* footer */
.footer{left:0;top:3113px;width:1200px;height:444px;background:var(--black)}
.foot-head{top:3172px;font-family:"Michroma",sans-serif;font-size:20px;color:var(--white)}
.foot-link{left:113px;font-size:15.5px;color:var(--white);display:flex;align-items:center;gap:12px}
.social{top:3386px;width:28px;height:28px;border-radius:50%;background:var(--blue)}
.vline{top:3201px;width:0;height:238px;border-left:1px dashed #777}
.info-icon{left:373px;width:30px;height:30px;border-radius:50%;background:var(--blue);display:flex;align-items:center;justify-content:center}
.info-label{left:416px;font-family:"Noto Sans",sans-serif;font-size:16.5px;color:var(--white)}
.info-value{left:416px;font-family:"Noto Sans",sans-serif;font-size:15.5px;color:var(--white)}
.dash{left:370px;width:242px;border-top:1px dashed #888}
.field{left:731px;width:353px;height:39px;border:1px solid #bbb;background:var(--black);color:var(--white);font-size:15px;padding:11px 13px;line-height:16px}
.submit{left:732px;top:3374px;width:352px;height:37px;background:var(--blue);color:var(--white);font-weight:700;font-size:16px;display:flex;align-items:center;justify-content:center}
.foot-rule{left:98px;top:3501px;width:1002px;border-top:1px solid #666}
.copyright{left:0;top:3517px;width:1200px;text-align:center;font-size:15px;color:var(--white)}
</style>
</head>
<body>

<!-- header -->
<div class="abs logo"><span class="logo-mark"></span><span class="logo-name">RIMCRAFT<small>WHEELWORKS</small></span></div>
<span class="abs nav display current" style="left:467px">Home</span>
<span class="abs nav-sep" style="left:546px">|</span>
<span class="abs nav display" style="left:576px">Services</span>
<span class="abs nav-sep" style="left:692px">|</span>
<span class="abs nav display" style="left:722px">Gallery</span>
<span class="abs nav-sep" style="left:832px">|</span>
<span class="abs nav display" style="left:862px">Clients</span>
<div class="abs contact-btn display">Contact</div>

<!-- hero -->
<div class="abs hero" role="img" aria-label="Mechanic rolling an alloy wheel with tyre across a workshop floor"></div>
<div class="abs hero-kicker display">Welcome to</div>
<div class="abs hero-title display">Rimcraft Wheel Works</div>
<p class="abs hero-text">Lorem ipsum dolor sit amet, consectetur adipiscing elit, sed do eiusmod tempor incididunt ut labore et dolore magna aliqua.</p>
<div class="abs hero-btn display">Get Started</div>

<!-- about -->
<h2 class="abs about-title display"><span class="accent">About</span> Rimcraft<br>Wheelworks</h2>
<p class="abs about-lead">Lorem ipsum dolor sit amet, consectetur adipiscing elit, sed do eiusmod tempor incididunt ut labore et dolore magna aliqua. Ut enim ad minim veniam, quis nostrud exercitation ullamco quis nostrud exercitation ullamco &nbsp;laboris nisi ut aliquip ex ea commodo consequat.</p>
<p class="abs about-body">Sed ut perspiciatis unde omnis iste natus error sit voluptatem accusantium doloremque laudantium, totam rem aperiam, eaque ipsa quae ab illo inventore veritatis et quasi architecto beatae vitae dicta sunt explicabo. Nemo enim ipsam voluptatem quia voluptas sit aspernatur aut odit aut fugit, sed quia consequuntur magni dolores eos qui ratione voluptatem sequi nesciunt. consectetur, adipisci velit, sed quia non numquam eius modi tempora incidunt ut labore et dolore magnam aliquam quaerat voluptatem.</p>
<div class="abs about-frame"></div>
<div class="photo about-back" role="img" aria-label="Technician in blue uniform tightening the nuts of an alloy wheel"></div>
<div class="photo about-front" role="img" aria-label="Gloved mechanic fitting a bronze alloy wheel in a garage"></div>

<!-- services -->
<div class="abs services"></div>
<h2 class="abs services-title display">Our Services</h2>
<div class="abs slider-dot" style="left:42px"><svg width="23" height="23" viewBox="0 0 23 23"><path d="M13 7l-4 4.5 4 4.5" fill="none" stroke="#fff" stroke-width="1.5"/></svg></div>
<div class="abs slider-dot" style="left:1125px"><svg width="23" height="23" viewBox="0 0 23 23"><path d="M10 7l4 4.5-4 4.5" fill="none" stroke="#fff" stroke-width="1.5"/></svg></div>

<div class="abs card" style="left:98px">
  <div class="photo card-img" style="background:linear-gradient(120deg,#c9c7c2,#7a8a6c 45%,#3a3a3a)" role="img" aria-label="Mechanic showing an alloy wheel to a customer"></div>
  <div class="abs card-tab display">Lorem Ipsum</div>
  <p class="abs card-text">Sed ut perspiciatis unde omnis iste<br>natus error sit laudantium.</p>
  <div class="abs card-link display">Read More<svg width="11" height="11" viewBox="0 0 11 11"><circle cx="5.5" cy="5.5" r="5.5" fill="#4688c9"/><path d="M4.5 3l2.5 2.5-2.5 2.5" fill="none" stroke="#fff" stroke-width="1.5"/></svg></div>
</div>
<div class="abs card" style="left:442px">
  <div class="photo card-img" style="background:linear-gradient(120deg,#2a2a2a,#8a8d92 45%,#3c4048)" role="img" aria-label="Mechanic inspecting a raised car wheel with a clipboard"></div>
  <div class="abs card-tab display">Lorem Ipsum</div>
  <p class="abs card-text">Sed ut perspiciatis unde omnis iste<br>natus error sit laudantium.</p>
  <div class="abs card-link display">Read More<svg width="11" height="11" viewBox="0 0 11 11"><circle cx="5.5" cy="5.5" r="5.5" fill="#4688c9"/><path d="M4.5 3l2.5 2.5-2.5 2.5" fill="none" stroke="#fff" stroke-width="1.5"/></svg></div>
</div>
<div class="abs card" style="left:784px">
  <div class="photo card-img" style="background:linear-gradient(120deg,#d8d4cc,#707a86 50%,#40464e)" role="img" aria-label="Mechanic working on the wheel of a grey car"></div>
  <div class="abs card-tab display">Lorem Ipsum</div>
  <p class="abs card-text">Sed ut perspiciatis unde omnis iste<br>natus error sit laudantium.</p>
  <div class="abs card-link display">Read More<svg width="11" height="11" viewBox="0 0 11 11"><circle cx="5.5" cy="5.5" r="5.5" fill="#4688c9"/><path d="M4.5 3l2.5 2.5-2.5 2.5" fill="none" stroke="#fff" stroke-width="1.5"/></svg></div>
</div>

<!-- gallery -->
<h2 class="abs gallery-title display"><span class="accent">Our</span> Gallery</h2>
<svg class="abs gallery-arrow" style="left:66px" width="12" height="20" viewBox="0 0 12 20"><path d="M9 3L3 10l6 7" fill="none" stroke="#999" stroke-width="1.6"/></svg>
<svg class="abs gallery-arrow" style="left:1123px" width="12" height="20" viewBox="0 0 12 20"><path d="M3 3l6 7-6 7" fill="none" stroke="#222" stroke-width="1.8"/></svg>
<div class="photo gallery-img" style="left:112px;background:linear-gradient(180deg,#3b4fa8,#8a8f9a 50%,#3a3a3c)" role="img" aria-label="Mechanic beside a stack of tyres on a lift"></div>
<div class="photo gallery-img" style="left:359px;background:linear-gradient(120deg,#e6e6e8,#9aa0a8 45%,#2b4f9a)" role="img" aria-label="Mechanic removing a wheel with an impact wrench"></div>
<div class="photo gallery-img" style="left:606px;background:linear-gradient(120deg,#2d44a8,#2a66c0 40%,#c9ccd0 70%,#333)" role="img" aria-label="Mechanic in blue and yellow overalls fitting a wheel"></div>
<div class="photo gallery-img" style="left:853px;background:linear-gradient(180deg,#2a3fb0,#6f7684 50%,#2f2f31)" role="img" aria-label="Mechanic mounting a tyre on a changing machine"></div>

<!-- testimonials -->
<div class="abs testimonials"></div>
<h2 class="abs testi-title display"><span class="accent">Client</span> Testimonials</h2>

<div class="abs testi-card" style="left:110px"><p class="testi-text">Sed ut perspiciatis unde omnis iste natus error sit voluptatem accusantium doloremque laudantium, totam rem aperiam, eaque ipsa</p></div>
<div class="abs testi-card" style="left:445px"><p class="testi-text">Sed ut perspiciatis unde omnis iste natus error sit voluptatem accusantium doloremque laudantium, totam rem aperiam, eaque ipsa</p></div>
<div class="abs testi-card" style="left:777px"><p class="testi-text">Sed ut perspiciatis unde omnis iste natus error sit voluptatem accusantium doloremque laudantium, totam rem aperiam, eaque ipsa</p></div>
<div class="abs avatar" style="left:219px" role="img" aria-label="Client portrait"></div>
<div class="abs avatar" style="left:553px" role="img" aria-label="Client portrait"></div>
<div class="abs avatar" style="left:886px" role="img" aria-label="Client portrait"></div>
<span class="abs testi-name" style="left:193px">Jhon Deo</span><span class="abs stars" style="left:279px">★★★★★</span>
<span class="abs testi-name" style="left:526px">Jhon Deo</span><span class="abs stars" style="left:612px">★★★★★</span>
<span class="abs testi-name" style="left:860px">Jhon Deo</span><span class="abs stars" style="left:946px">★★★★★</span>

<!-- footer -->
<div class="abs footer"></div>
<h3 class="abs foot-head" style="left:113px">Quick Links</h3>
<div class="abs foot-link" style="top:3214px"><svg width="14" height="12" viewBox="0 0 14 12"><path d="M1 6h11M7 1l5 5-5 5" fill="none" stroke="#fff" stroke-width="2.2"/></svg>Home</div>
<div class="abs foot-link" style="top:3245px"><svg width="14" height="12" viewBox="0 0 14 12"><path d="M1 6h11M7 1l5 5-5 5" fill="none" stroke="#fff" stroke-width="2.2"/></svg>Services</div>
<div class="abs foot-link" style="top:3276px"><svg width="14" height="12" viewBox="0 0 14 12"><path d="M1 6h11M7 1l5 5-5 5" fill="none" stroke="#fff" stroke-width="2.2"/></svg>Gallery,</div>
<div class="abs foot-link" style="top:3307px"><svg width="14" height="12" viewBox="0 0 14 12"><path d="M1 6h11M7 1l5 5-5 5" fill="none" stroke="#fff" stroke-width="2.2"/></svg>Clients</div>
<div class="abs foot-link" style="top:3338px"><svg width="14" height="12" viewBox="0 0 14 12"><path d="M1 6h11M7 1l5 5-5 5" fill="none" stroke="#fff" stroke-width="2.2"/></svg>Contact</div>
<span class="abs social" style="left:113px"></span>
<span class="abs social" style="left:152px"></span>
<span class="abs social" style="left:189px"></span>
<span class="abs social" style="left:226px"></span>

<div class="abs vline" style="left:316px"></div>
<h3 class="abs foot-head" style="left:370px">Contact Details</h3>
<div class="abs info-icon" style="top:3219px"><svg width="14" height="14" viewBox="0 0 24 24"><path d="M6.6 10.8a15 15 0 0 0 6.6 6.6l2.2-2.2c.3-.3.7-.4 1-.2 1.1.4 2.3.6 3.6.6.6 0 1 .4 1 1V20c0 .6-.4 1-1 1A17 17 0 0 1 3 4c0-.6.4-1 1-1h3.5c.6 0 1 .4 1 1 0 1.3.2 2.5.6 3.6.1.3 0 .7-.2 1z" fill="#fff"/></svg></div>
<span class="abs info-label" style="top:3216px">Phone;</span>
<span class="abs info-value" style="top:3247px">+1 555 0142 7788</span>
<div class="abs dash" style="top:3283px"></div>
<div class="abs info-icon" style="top:3302px"><svg width="14" height="12" viewBox="0 0 14 12"><rect x="0.5" y="1" width="13" height="10" fill="#fff"/><path d="M1 1.5l6 5 6-5" fill="none" stroke="#4688c9" stroke-width="1.3"/></svg></div>
<span class="abs info-label" style="top:3298px">Email:</span>
<span class="abs info-value" style="top:3330px">info@rimcraftwheels.example</span>
<div class="abs dash" style="top:3364px"></div>
<div class="abs info-icon" style="top:3385px"><svg width="12" height="15" viewBox="0 0 12 16"><path d="M6 0a6 6 0 0 0-6 6c0 4.5 6 10 6 10s6-5.5 6-10a6 6 0 0 0-6-6z" fill="#fff"/><circle cx="6" cy="6" r="2.2" fill="#4688c9"/></svg></div>
<span class="abs info-label" style="top:3390px">Address:</span>
<span class="abs info-value" style="top:3418px">Rimcraft Wheelworks</span>
<span class="abs info-value" style="top:3444px">Harbor County.</span>

<div class="abs vline" style="left:685px"></div>
<h3 class="abs foot-head" style="left:731px">Contact Me</h3>
<div class="abs field" style="top:3215px">Name:</div>
<div class="abs field" style="top:3267px">Email:</div>
<div class="abs field" style="top:3320px">Address:</div>
<div class="abs submit">Submit Now</div>

<div class="abs foot-rule"></div>
<p class="abs copyright">Copyrights@2023. Rimcraft Wheel Works.All Rights Reserved</p>

</body>
</html>
```